Lip balm label

4 different kinds with a blend of essential oils. Cravings, Energy, Anxiety and Sensual. No preservatives or engineered products. Need different colored labels for each one. Maybe lavender or purple for stress, green or orange for appetite, red for energy and black for sensual. Or just use your professional judgement. Must fit on small lip balm tube

Target Market(s)

Young and old adults

Industry/Entity Type

Cosmetics

Logo Text

Mouthgrove

Logo styles of interest
Wordmark Logo
Font styles to use
Decorative

Requirements
Must have
• Name of company (KoRu Organics), 100% Organic, list of ingredients in each one, weight is 0.15 oz, made with Essential Oils, soothing and moisturizing,
• Lip Balm
Nice to have
• Made in USA, satisfaction guaranteed

```html
<!DOCTYPE html>
<html lang="en">
<head>
<meta charset="utf-8">
<title>Mouthgrove Lip Balm Labels</title>
<link rel="stylesheet" href="https://fonts.googleapis.com/css2?family=PT+Sans+Narrow:wght@400;700&family=Arimo:wght@400;700&display=swap">
<style>
  :root {
    --gold: #c9a96e;
    --page: #ffffff;
    --sensual: #000000;
    --energy: #9a0f07;
    --anxiety: #420a46;
    --cravings: #1f3b12;
    --display: "PT Sans Narrow", sans-serif;
    --body: "Arimo", sans-serif;
  }
  * { margin: 0; padding: 0; box-sizing: border-box; }
  html, body { width: 1200px; height: 1000px; overflow: hidden; background: var(--page); }
  .sheet { position: relative; width: 1200px; height: 1000px; }

  .label {
    position: absolute; left: 175px; width: 850px; height: 219px;
    color: var(--gold); overflow: hidden;
  }
  .label::before, .label::after {
    content: ""; position: absolute; top: 0; bottom: 0; width: 16px; background: var(--gold);
  }
  .label::before { left: 0; }
  .label::after { right: 0; }

  .label--sensual  { top: 22px;  background: var(--sensual); }
  .label--energy   { top: 266px; background: var(--energy); }
  .label--anxiety  { top: 512px; background: var(--anxiety); }
  .label--cravings { top: 758px; background: var(--cravings); }

  .brand {
    position: absolute; left: 60px; top: 36px; width: 296px; text-align: center;
  }
  .brand__name {
    font-family: var(--display); font-weight: 400; font-size: 50px; line-height: 1;
  }
  .brand__tag {
    font-family: var(--display); font-size: 18px; line-height: 1; margin-top: 4px;
    padding-left: 90px;
  }

  .variant {
    position: absolute; left: 420px; top: 46px; width: 306px; text-align: center;
    font-family: var(--display); font-size: 52px; line-height: 1;
  }
  .claim {
    position: absolute; left: 400px; top: 115px; width: 346px; text-align: center;
    font-family: var(--display); font-size: 10.5px; letter-spacing: 0.9px;
  }

  .maker {
    position: absolute; left: 44px; top: 180px;
    font-family: var(--display); font-size: 24px; line-height: 1;
  }
  .ingredients {
    position: absolute; left: 200px; top: 174px; width: 490px;
    font-family: var(--body); font-size: 9px; line-height: 12.5px;
  }
  .ingredients strong { font-weight: 700; }

  .origin {
    position: absolute; left: 709px; top: 184px; width: 77px; height: 21px;
    border: 1px solid var(--gold); border-radius: 10px; text-align: center;
    font-family: var(--body);
  }
  .origin__main { display: block; font-size: 8.5px; letter-spacing: 0.8px; line-height: 10px; margin-top: 1px; }
  .origin__sub { display: block; font-size: 5px; line-height: 6px; }

  .weight {
    position: absolute; left: 806px; top: 176px; width: 26px; text-align: center;
    font-family: var(--display); font-size: 14px; white-space: nowrap;
    transform: rotate(-90deg); transform-origin: center;
  }
</style>
</head>
<body>
<main class="sheet">

  <section class="label label--sensual">
    <div class="brand"><div class="brand__name">Mouthgrove</div><div class="brand__tag">100% Organic Lip Balm</div></div>
    <h2 class="variant">Sensual</h2>
    <p class="claim">MADE WITH ESSENTIAL OILS, SOOTHING AND MOISTURIZING</p>
    <p class="maker">KoRu Organics</p>
    <p class="ingredients"><strong>100% Organic ingredients:</strong> Lorem ipsum dolor sit amet, consectetur adipiscing elit, sed do eiusmod tempor incidi-dunt ut labore et dolore magna aliqua. Ut enim ad minim veniam, quis nostrud exercitation ullamco laboris nisi ut aliquip ex ea commodo consequat.</p>
    <div class="origin"><span class="origin__main">MADE IN USA</span><span class="origin__sub">Satisfaction guaranteed</span></div>
    <p class="weight">0.15 oz</p>
  </section>

  <section class="label label--energy">
    <div class="brand"><div class="brand__name">Mouthgrove</div><div class="brand__tag">100% Organic Lip Balm</div></div>
    <h2 class="variant">Energy</h2>
    <p class="claim">MADE WITH ESSENTIAL OILS, SOOTHING AND MOISTURIZING</p>
    <p class="maker">KoRu Organics</p>
    <p class="ingredients"><strong>100% Organic ingredients:</strong> Lorem ipsum dolor sit amet, consectetur adipiscing elit, sed do eiusmod tempor incidi-dunt ut labore et dolore magna aliqua. Ut enim ad minim veniam, quis nostrud exercitation ullamco laboris nisi ut aliquip ex ea commodo consequat.</p>
    <div class="origin"><span class="origin__main">MADE IN USA</span><span class="origin__sub">Satisfaction guaranteed</span></div>
    <p class="weight">0.15 oz</p>
  </section>

  <section class="label label--anxiety">
    <div class="brand"><div class="brand__name">Mouthgrove</div><div class="brand__tag">100% Organic Lip Balm</div></div>
    <h2 class="variant">Anxiety</h2>
    <p class="claim">MADE WITH ESSENTIAL OILS, SOOTHING AND MOISTURIZING</p>
    <p class="maker">KoRu Organics</p>
    <p class="ingredients"><strong>100% Organic ingredients:</strong> Lorem ipsum dolor sit amet, consectetur adipiscing elit, sed do eiusmod tempor incidi-dunt ut labore et dolore magna aliqua. Ut enim ad minim veniam, quis nostrud exercitation ullamco laboris nisi ut aliquip ex ea commodo consequat.</p>
    <div class="origin"><span class="origin__main">MADE IN USA</span><span class="origin__sub">Satisfaction guaranteed</span></div>
    <p class="weight">0.15 oz</p>
  </section>

  <section class="label label--cravings">
    <div class="brand"><div class="brand__name">Mouthgrove</div><div class="brand__tag">100% Organic Lip Balm</div></div>
    <h2 class="variant">Cravings</h2>
    <p class="claim">MADE WITH ESSENTIAL OILS, SOOTHING AND MOISTURIZING</p>
    <p class="maker">KoRu Organics</p>
    <p class="ingredients"><strong>100% Organic ingredients:</strong> Lorem ipsum dolor sit amet, consectetur adipiscing elit, sed do eiusmod tempor incidi-dunt ut labore et dolore magna aliqua. Ut enim ad minim veniam, quis nostrud exercitation ullamco laboris nisi ut aliquip ex ea commodo consequat.</p>
    <div class="origin"><span class="origin__main">MADE IN USA</span><span class="origin__sub">Satisfaction guaranteed</span></div>
    <p class="weight">0.15 oz</p>
  </section>

</main>
</body>
</html>
```